Real Estate Business Card

On the front side I want to have my info, my brokerage info.
On the back side I want have my complany’s logo, website and Facebook link. I will provide all this once I select a design.

I would like to see Black background and gold text, Dark Blue and gold text and White and blue text designs

Font styles to use
Sans Serif
Script

```html
<!DOCTYPE html>
<html lang="en">
<head>
<meta charset="utf-8">
<title>Northvale Real Estate – Business Card</title>
<link href="https://fonts.googleapis.com/css2?family=Montserrat:wght@800&family=Roboto:wght@400;500;700&display=swap" rel="stylesheet">
<style>
  :root {
    --backdrop: #2a2a2c;
    --card-black: #1b1b1d;
    --brand-slate: #6e7689;
    --brand-red: #c8262d;
    --band-red-start: #b92429;
    --band-red-end: #ee4448;
    --gold: #ecd27a;
    --white: #ffffff;
  }
  * { box-sizing: border-box; margin: 0; padding: 0; }
  html, body {
    width: 1200px; height: 900px; overflow: hidden;
    background: var(--backdrop);
  }
  .canvas { position: relative; width: 1200px; height: 900px; }
  .card {
    position: absolute;
    width: 720px; height: 411px;
    background: var(--card-black);
    overflow: hidden;
    box-shadow: 0 6px 18px rgba(0,0,0,.45);
  }
  .card--back { left: 300px; top: 40px; }
  .card--front { left: 180px; top: 470px; }

  .brand {
    position: absolute;
    display: flex; align-items: center; gap: 12px;
    font-family: "Montserrat", sans-serif;
    font-weight: 800;
    color: var(--brand-slate);
    white-space: nowrap;
    line-height: 1;
  }
  .brand__square { background: var(--brand-red); flex: none; }
  .card--back .brand { right: 48px; bottom: 58px; font-size: 30px; }
  .card--back .brand__square { width: 22px; height: 22px; }
  .card--front .brand { left: 80px; top: 120px; font-size: 34px; }
  .card--front .brand__square { width: 26px; height: 26px; }

  .band { position: absolute; left: 0; top: 0; width: 720px; height: 411px; }

  .contact-list {
    position: absolute; left: 58px; top: 258px;
    list-style: none;
    font-family: "Roboto", sans-serif;
    font-size: 17px; color: var(--white);
    line-height: 23px;
  }
  .contact-list li { display: flex; align-items: center; gap: 10px; }
  .contact-list svg { width: 14px; height: 14px; flex: none; }

  .person {
    position: absolute; right: 40px; top: 212px;
    text-align: right;
    font-family: "Roboto", sans-serif;
    line-height: 1.2;
  }
  .person__name { font-size: 26px; font-weight: 700; color: var(--gold); letter-spacing: .5px; }
  .person__role { font-size: 19px; font-weight: 500; color: var(--brand-red); }

  .address {
    position: absolute; right: 40px; bottom: 28px;
    text-align: right;
    font-family: "Roboto", sans-serif;
    font-style: normal;
    font-size: 19px; font-weight: 500; color: var(--white);
    line-height: 24px;
  }
</style>
</head>
<body>
<main class="canvas">

  <section class="card card--back" aria-label="Card back">
    <div class="brand"><span class="brand__square"></span>NORTHVALE REAL ESTATE</div>
  </section>

  <section class="card card--front" aria-label="Card front">
    <div class="brand"><span class="brand__square"></span>NORTHVALE REAL ESTATE</div>

    <svg class="band" viewBox="0 0 720 411" aria-hidden="true">
      <defs>
        <linearGradient id="bandFill" x1="0" y1="0" x2="1" y2="0">
          <stop offset="0" stop-color="#b92429"/>
          <stop offset="1" stop-color="#ee4448"/>
        </linearGradient>
      </defs>
      <polygon points="0,242 258,242 268,298 720,298 720,411 0,411" fill="url(#bandFill)"/>
      <polyline points="0,242 258,242 268,298 720,298" fill="none" stroke="#ffffff" stroke-width="2"/>
    </svg>

    <ul class="contact-list">
      <li>
        <svg viewBox="0 0 16 16" aria-hidden="true"><path d="M4 1l3 3-1.6 2a9 9 0 0 0 4.6 4.6L12 9l3 3-2 2.5C7 14 2 9 1.5 3z" fill="#ecd27a"/></svg>
        555 214 0387
      </li>
      <li>
        <svg viewBox="0 0 16 16" aria-hidden="true"><rect x="1" y="3" width="14" height="10" fill="#ecd27a"/><path d="M1 3l7 6 7-6" fill="none" stroke="#b92429" stroke-width="1.4"/></svg>
        daniel@northvale.com
      </li>
      <li>
        <svg viewBox="0 0 16 16" aria-hidden="true"><circle cx="8" cy="8" r="6.5" fill="none" stroke="#ecd27a" stroke-width="1.6"/><path d="M1.5 8h13M8 1.5c3 3.5 3 9.5 0 13M8 1.5c-3 3.5-3 9.5 0 13" fill="none" stroke="#ecd27a" stroke-width="1.2"/></svg>
        www.northvale.com
      </li>
      <li>
        <svg viewBox="0 0 16 16" aria-hidden="true"><circle cx="8" cy="8" r="7" fill="#ecd27a"/></svg>
        /northvale
      </li>
    </ul>

    <div class="person">
      <p class="person__name">DANIEL REYES</p>
      <p class="person__role">CEO/FOUNDER</p>
    </div>

    <address class="address">
      2140 Willow Crest Drive<br>
      Fairbanks, Alaska 99701
    </address>
  </section>

</main>
</body>
</html>
```